Garlic Farm for Farm Sales/Restaurant sales

Need a professional, but appealing to agriculture world. We are selling 27 kinds of Organic Garlic from a farm in Simla,CO. I have uploaded logo and business information-we are going to need a template, because I will need to use it for four separate people.
-We are trying to appeal to Farm to table restaurants
-As well as growers/farmers

Target Market(s)

Agriculture Sales/Restaurants-Organic

Industry/Entity Type

Agriculture

Contact Information for Business Card

Want it to look more unique then your average kelto stock card- I want it to look amazing

Font styles to use
Sans Serif

Colors
0455a3
ec1f27
fbed22
ffffff

Requirements
Must have
• Just be creative
Nice to have
• Colorful
Should not have
• plain

```html
<!DOCTYPE html>
<html lang="en">
<head>
<meta charset="utf-8">
<title>Summit Crest Garlic – Business Card</title>
<link href="https://fonts.googleapis.com/css2?family=Josefin+Sans:wght@400;600;700&display=swap" rel="stylesheet">
<style>
  :root {
    --navy: #1b3263;
    --red: #d5232b;
    --yellow: #fbd80b;
    --white: #ffffff;
    --stage: #e7e8ea;
    --ink: #1b3263;
  }
  * { margin: 0; padding: 0; box-sizing: border-box; }
  html, body {
    width: 1200px; height: 900px; overflow: hidden;
    background: var(--stage);
    font-family: "Josefin Sans", sans-serif;
  }
  .canvas { position: relative; width: 1200px; height: 900px; }
  .card {
    position: absolute; width: 700px; height: 400px;
    box-shadow: 0 6px 18px rgba(0,0,0,.18);
    overflow: hidden;
  }
  /* Back side */
  .card-back { left: 140px; top: 40px; background: var(--navy); }
  .brand {
    position: absolute; display: flex; align-items: center; gap: 14px;
  }
  .brand-dot { width: 64px; height: 64px; border-radius: 50%; background: var(--red); flex: none; }
  .brand-name { font-weight: 700; font-size: 34px; letter-spacing: .5px; }
  .card-back .brand { right: 60px; top: 110px; }
  .card-back .brand-name { color: var(--white); }
  .social {
    position: absolute; right: 70px; top: 210px; display: flex; gap: 34px;
  }
  .social span {
    width: 24px; height: 24px; border-radius: 50%; background: var(--white); display: block;
  }
  .stripe {
    position: absolute; left: 0; bottom: 62px; width: 420px; height: 26px; background: var(--yellow);
  }
  /* Front side */
  .card-front { left: 360px; top: 470px; background: var(--white); }
  .card-front .brand { right: 50px; top: 40px; }
  .card-front .brand-name { color: var(--navy); }
  .rule {
    position: absolute; left: 330px; right: 0; top: 150px; height: 8px; background: var(--red);
  }
  .person {
    position: absolute; left: 40px; top: 310px;
    font-size: 34px; font-weight: 600; letter-spacing: 2px; color: var(--navy);
  }
  .person .last { color: var(--red); }
  .contact {
    position: absolute; right: 40px; top: 180px; list-style: none;
    text-align: right; color: var(--ink); font-size: 17px; line-height: 30px;
  }
  .contact li { display: flex; justify-content: flex-end; align-items: center; gap: 10px; }
  .contact .icon {
    width: 20px; height: 20px; background: var(--red); border-radius: 3px;
    display: inline-flex; align-items: center; justify-content: center;
  }
  .contact .spacer { width: 20px; }
  .contact .hl { color: var(--red); }
</style>
</head>
<body>
<main class="canvas">
  <section class="card card-back" aria-label="Card back">
    <div class="brand">
      <span class="brand-dot"></span>
      <span class="brand-name">summit crest garlic</span>
    </div>
    <div class="social" aria-label="Social profiles">
      <span></span><span></span><span></span><span></span>
    </div>
    <div class="stripe"></div>
  </section>

  <section class="card card-front" aria-label="Card front">
    <div class="brand">
      <span class="brand-dot"></span>
      <span class="brand-name">summit crest garlic</span>
    </div>
    <div class="rule"></div>
    <ul class="contact">
      <li>P.O. Box 48 Larkton, CO 80912 <span class="spacer"></span></li>
      <li>719-555-0143
        <span class="icon"><svg width="12" height="12" viewBox="0 0 24 24"><path fill="#fff" d="M6.6 10.8a15 15 0 0 0 6.6 6.6l2.2-2.2c.3-.3.7-.4 1-.2 1.1.4 2.3.6 3.6.6.6 0 1 .4 1 1V20c0 .6-.4 1-1 1A17 17 0 0 1 3 4c0-.6.4-1 1-1h3.5c.6 0 1 .4 1 1 0 1.3.2 2.5.6 3.6.1.3 0 .7-.2 1z"/></svg></span>
      </li>
      <li>Nora@SCGarlic.com
        <span class="icon"><svg width="12" height="12" viewBox="0 0 24 24"><rect x="2" y="5" width="20" height="14" rx="1" fill="none" stroke="#fff" stroke-width="2"/><path d="M2 6l10 7 10-7" fill="none" stroke="#fff" stroke-width="2"/></svg></span>
      </li>
      <li>www.<span class="hl">SC</span>Garlic.com
        <span class="icon"><svg width="12" height="12" viewBox="0 0 24 24"><g fill="none" stroke="#fff" stroke-width="2"><circle cx="12" cy="12" r="9"/><ellipse cx="12" cy="12" rx="4" ry="9"/><path d="M3 12h18"/></g></svg></span>
      </li>
    </ul>
    <p class="person">NORA <span class="last">FENWICK</span></p>
  </section>
</main>
</body>
</html>
```